Health Wellbeing Beauty online Shop

I have attached a full spec, however in summary this is a new business startup selling skincare products.

We need a web design for new wellbeing website, selling skincare products so need an eCommerce solution . On the home page I would like these faces to dissolve into each other on a loop or use a honeycomb style transation.
You will need the option of being able to log into an account, either through lumigram, vexora, chirplo or create an account. For created accounts, obviously need the facility to be able to reset passwords, see previous orders, track current order, and maintain favourites.
It should be PC, mobile and tablet friendly.

Look and Feel
It should be an elegant, modern, professional, trendy, unisex website. It should look clean and calm. Am happy to try interesting and slightly unusual designs. I would also like to have chat functionality, either powered by talvuNchat or by Quo 58.
Websites I like are
https://www.nobel-radiance.example.co.uk/
https://www.mereminerals.example.co.uk/
http://www.brightdermis.example.com/

PLEASE DO USE YOUR KNOWELDGE OF WHAT WORKS FOR WEB DESIGN. YOU’RE THE EXPERT AND NEED YOUR EXPERTISE. CARTE BLANCHE TO DESIGN AS YOU SEE FIT. Please be creative, I need my site to stand out from the crowd.

Target Market(s)

Target Market
Middle aged women are our most common client, however, younger patients, both male and female, will often visit the site. In summary, I would like the site to appeal to all age brackets.

Industry/Entity Type

Business

Coding

Coded - Design and coding required

Number of Pages Required

4 page

Requirements
Must have
• Need shop to be exactly like shop on this link http://www.brightdermis.example.com/
Nice to have
• i would like something unique and creative

```html
<!DOCTYPE html>
<html lang="en">
<head>
<meta charset="utf-8">
<title>Velique Skin Clinic</title>
<link href="https://fonts.googleapis.com/css2?family=Roboto:ital,wght@0,300;0,400;0,500;0,700;1,400&family=Lato:ital,wght@0,400;0,700;1,400&display=swap" rel="stylesheet">
<style>
:root{
  --ink:#1e1e1e;
  --text:#555;
  --muted:#8a8a8a;
  --line:#e3e3e3;
  --page:#f4f4f4;
  --white:#fff;
  --nav-top:#8c8c8c;
  --nav-bottom:#6a6a6a;
  --nav-active:#4e4e4e;
  --lumigram:#3b5a9a;
  --star:#f3a521;
  --icon-grey:#9a9a9a;
  --sidebar-head:#5c5c5c;
  --footer-top:#8e8e8e;
  --footer-bottom:#5a5a5a;
}
*{box-sizing:border-box;margin:0;padding:0}
html,body{width:1200px;height:2432px;overflow:hidden}
body{position:relative;background:var(--white);font-family:"Roboto",Arial,sans-serif;color:var(--ink)}
.abs{position:absolute}

/* Header */
.site-header{position:absolute;left:0;top:0;width:1200px;height:165px;background:var(--white)}
.btn-account{left:75px;top:40px;width:170px;height:36px;border:2px solid #444;border-radius:18px;font-size:12px;font-weight:500;text-align:center;line-height:32px;letter-spacing:.3px}
.btn-social-login{left:75px;top:92px;width:197px;height:38px;background:var(--lumigram);border-radius:19px;color:var(--white);font-size:14px;line-height:38px;padding-left:46px}
.btn-social-login .dot{position:absolute;left:22px;top:14px;width:10px;height:10px;border-radius:50%;background:var(--white)}
.brand{left:450px;top:56px;width:300px;text-align:center}
.brand-name{font-size:36px;font-weight:500;letter-spacing:6px;color:#3a3a3a}
.cart{left:880px;top:57px}
.cart-title{left:942px;top:66px;font-size:12px;font-weight:700;color:#333}
.cart-count{left:942px;top:84px;font-size:11px;color:var(--muted)}
.search{left:1087px;top:62px;width:38px;height:38px;border-radius:50%;background:var(--icon-grey)}

/* Navigation */
.main-nav{position:absolute;left:0;top:165px;width:1200px;height:54px;background:linear-gradient(var(--nav-top),var(--nav-bottom))}
.main-nav .item{position:absolute;top:0;height:54px;line-height:54px;color:var(--white);font-size:13.5px;transform:translateX(-50%);white-space:nowrap}
.main-nav .active{left:75px;width:102px;transform:none;text-align:center;background:var(--nav-active)}

/* Hero */
.hero{position:absolute;left:0;top:219px;width:1200px;height:470px;background:linear-gradient(100deg,#efe6e6 0%,#f1e8e6 45%,#e8dede 100%)}
.hero-title{left:75px;top:136px;font-size:44px;font-weight:500;color:#222}
.hero-text{left:75px;top:206px;width:510px;font-family:"Lato",sans-serif;font-style:italic;font-size:13.5px;line-height:22px;color:#7d7575}
.hero-dots{left:75px;top:316px;display:flex;gap:9px}
.hero-dots span{width:15px;height:15px;border-radius:50%;background:#4a4a4a;border:2px solid #4a4a4a}
.hero-dots span:first-child{background:transparent}
.hero-faces{left:715px;top:34px}

/* Shop */
.shop{position:absolute;left:0;top:689px;width:1200px;height:941px;background:var(--page)}
.sidebar{left:75px;top:84px;width:241px;height:659px;background:var(--white)}
.sidebar-head{height:46px;background:var(--sidebar-head);color:var(--white);font-size:18px;font-weight:500;line-height:46px;padding-left:22px}
.filter-title{position:absolute;left:22px;font-size:12px;font-weight:500;color:#222}
.filter-title::before{content:"";display:inline-block;margin-right:8px;vertical-align:2px;border-left:4px solid transparent;border-right:4px solid transparent;border-top:5px solid #222}
.filter-item{position:absolute;left:24px;font-size:12.5px;color:var(--muted)}
.filter-item::before{content:"";display:inline-block;width:10px;height:10px;background:#eee;border:1px solid #e2e2e2;margin-right:14px;vertical-align:-1px}
.divider{position:absolute;left:22px;width:197px;height:1px;background:var(--line)}
.price-label{position:absolute;font-size:12px;color:#333}
.featured-title{left:352px;top:88px;font-size:18px;font-weight:700;color:#222}
.sort-label{left:931px;top:90px;font-size:12px;color:#444}
.sort-select{left:992px;top:80px;width:132px;height:34px;border:1px solid #e5e5e5;border-radius:17px;background:var(--white);font-size:12px;font-style:italic;color:#aaa;line-height:32px;padding-left:20px}
.sort-select::after{content:"";position:absolute;right:18px;top:15px;border-left:4px solid transparent;border-right:4px solid transparent;border-top:5px solid #888}

.product-card{position:absolute;width:374px;height:217px;background:var(--white)}
.product-photo{position:absolute;left:26px;top:24px;width:120px;height:170px;border-radius:6px}
.product-name{position:absolute;left:167px;top:27px;font-size:16px;font-weight:500;color:#222}
.product-rating{position:absolute;left:167px;top:55px;display:flex;align-items:center;gap:10px;font-size:8px;color:#999}
.product-from{position:absolute;left:167px;top:92px;font-size:15px;font-weight:500;color:#222}
.product-price{position:absolute;left:167px;top:112px;font-size:24px;font-weight:700;color:#222}
.product-price small{font-size:12px;font-weight:400;color:#555}
.btn-quick{position:absolute;left:167px;top:161px;width:117px;height:34px;border:2px solid #999;border-radius:17px;font-size:11px;color:#777;text-align:center;line-height:30px;letter-spacing:.4px}
.btn-cart{position:absolute;left:305px;top:162px;width:32px;height:32px;border-radius:50%;background:var(--icon-grey)}

/* Reviews */
.reviews{position:absolute;left:0;top:1630px;width:1200px;height:352px;background:radial-gradient(ellipse at 55% 40%,#3d4248 0%,#272a2e 55%,#1c1d20 100%)}
.reviews-title{left:0;top:66px;width:1200px;text-align:center;font-size:20px;font-weight:700;color:var(--white)}
.review-quote{left:440px;top:120px;font-family:"Georgia",serif;font-size:44px;font-weight:700;color:var(--white);line-height:1}
.review-text{left:440px;top:160px;width:525px;font-family:"Lato",sans-serif;font-style:italic;font-size:13.5px;line-height:24px;color:#d6d6d6}
.review-name{left:440px;top:252px;font-size:14px;font-weight:500;color:var(--white)}
.review-name em{font-family:"Lato",sans-serif;font-weight:400;margin-left:12px;color:#ddd}

/* Footer */
.site-footer{position:absolute;left:0;top:1982px;width:1200px;height:450px;background:linear-gradient(var(--footer-top),var(--footer-bottom))}
.footer-heading{position:absolute;top:72px;font-size:15px;font-weight:700;color:var(--white)}
.quick-links{position:absolute;left:75px;top:120px;list-style:none}
.quick-links li{height:27.6px;font-size:12.5px;color:var(--white);padding-left:27px;position:relative}
.quick-links li::before{content:"";position:absolute;left:0;top:3px;width:11px;height:11px;border-radius:50%;background:var(--white)}
.quick-links li::after{content:"";position:absolute;left:3px;top:6px;border-top:2.5px solid transparent;border-bottom:2.5px solid transparent;border-left:4px solid #777}
.social-link{position:absolute;left:342px;font-size:12.5px;color:var(--white)}
.social-link::before{content:"";display:inline-block;width:12px;height:12px;border-radius:50%;background:var(--white);margin-right:14px;vertical-align:-1px}
.footer-text{position:absolute;font-size:12px;line-height:19px;color:var(--white)}
.phone-icon{position:absolute;left:558px}
.phone-label{position:absolute;left:611px;font-size:12px;color:var(--white)}
.phone-number{position:absolute;left:611px;font-size:20px;color:var(--white)}
.btn-send{left:890px;top:2251px;width:90px;height:34px;background:var(--white);border-radius:17px;font-size:11px;font-weight:700;line-height:34px;text-align:center;color:#333}
.copyright{left:0;top:2383px;width:1200px;text-align:center;font-size:12px;color:var(--white)}
</style>
</head>
<body>

<header class="site-header">
  <div class="abs btn-account">CREATE AN ACCOUNT</div>
  <div class="abs btn-social-login"><span class="dot"></span>Login with lumigram</div>
  <div class="abs brand">
    <div class="brand-name">VELIQUE</div>
  </div>
  <svg class="abs cart" width="50" height="48" viewBox="0 0 50 48" aria-hidden="true">
    <circle cx="22" cy="26" r="20" fill="none" stroke="#9a9a9a" stroke-width="2"/>
    <path d="M11 22h22l-3 12H14z" fill="#9a9a9a"/>
    <path d="M16 22l4-7M28 22l-4-7" stroke="#9a9a9a" stroke-width="2" fill="none"/>
    <circle cx="40" cy="9" r="9" fill="#8a8a8a"/>
    <text x="40" y="13" font-size="11" fill="#fff" text-anchor="middle" font-family="Roboto,sans-serif">0</text>
  </svg>
  <div class="abs cart-title">SHOPPING CART</div>
  <div class="abs cart-count">(0) Items</div>
  <div class="abs search">
    <svg width="38" height="38" viewBox="0 0 38 38" aria-hidden="true">
      <circle cx="17" cy="17" r="6" fill="none" stroke="#fff" stroke-width="2.4"/>
      <path d="M21.5 21.5l5 5" stroke="#fff" stroke-width="2.6" stroke-linecap="round"/>
    </svg>
  </div>
</header>

<nav class="main-nav">
  <div class="item active">Home</div>
  <div class="item" style="left:279px">Skin Lightening Tablets</div>
  <div class="item" style="left:467px">Skin Lightening Creams</div>
  <div class="item" style="left:655px">Skin Lightening Soaps</div>
  <div class="item" style="left:835px">Skin Lightening Vials</div>
  <div class="item" style="left:977px">Contact</div>
  <div class="item" style="left:1081px">About Us</div>
</nav>

<section class="hero" role="img" aria-label="Soft blurred pale pink flower backdrop">
  <h1 class="abs hero-title">Velique Skin Clinic</h1>
  <p class="abs hero-text">Lorem ipsum dolor sit amet, consectetur adipiscing elit. Phasellus non sodales ipsum. Pellentesque ac nisi eu sem suscipit luctus. Duis commodo aliquam mi, non pellentesque &nbsp;amet, consectetur.</p>
  <div class="abs hero-dots"><span></span><span></span><span></span><span></span></div>
  <svg class="abs hero-faces" width="380" height="400" viewBox="0 0 380 400">
    <polygon role="img" aria-label="Portrait of a fair-haired woman" points="6,193 58,100 164,100 216,193 164,286 58,286" fill="#d9b9a6" stroke="#fff" stroke-width="3"/>
    <polygon role="img" aria-label="Portrait of a smiling woman" points="166,97 218,4 324,4 376,97 324,190 218,190" fill="#c99a86" stroke="#fff" stroke-width="3"/>
    <polygon role="img" aria-label="Portrait of a dark-haired woman" points="166,287 218,194 324,194 376,287 324,380 218,380" fill="#8a5a44" stroke="#fff" stroke-width="3"/>
  </svg>
</section>

<section class="shop">
  <aside class="abs sidebar">
    <div class="sidebar-head">Refined By</div>
    <div class="filter-title" style="top:80px">PRODUCT TYPE</div>
    <div class="filter-item" style="top:125px">Skin Lightening tablets</div>
    <div class="filter-item" style="top:159px">Skin Lightening Creams</div>
    <div class="filter-item" style="top:191px">Skin Lightening Soaps</div>
    <div class="filter-item" style="top:225px">Skin Lightening Vials</div>
    <div class="filter-item" style="top:258px">Skin Lightening Systems</div>
    <div class="divider" style="top:294px"></div>
    <div class="filter-title" style="top:324px">PRICE RANGE</div>
    <div class="price-label" style="left:22px;top:362px">$5</div>
    <div class="price-label" style="left:186px;top:362px">$210</div>
    <svg class="abs" style="left:18px;top:380px" width="206" height="16" viewBox="0 0 206 16" aria-hidden="true">
      <rect x="4" y="5" width="198" height="3" fill="#ccc"/>
      <path d="M0 15V8l4-5 4 5v7z" fill="#666"/>
      <path d="M198 15V8l4-5 4 5v7z" fill="#888"/>
    </svg>
    <div class="divider" style="top:437px"></div>
    <div class="filter-title" style="top:472px">SHOP BY</div>
    <div class="filter-item" style="top:509px">Vitamins</div>
    <div class="filter-item" style="top:543px">Supplements</div>
    <div class="filter-item" style="top:575px">Nutrient Reference</div>
    <div class="filter-item" style="top:609px">Not Applicable</div>
  </aside>

  <h2 class="abs featured-title">FEATURED PRODUCT</h2>
  <div class="abs sort-label">Sort By</div>
  <div class="abs sort-select">Top Sellers</div>

  <article class="product-card" style="left:352px;top:145px">
    <div class="product-photo" role="img" aria-label="Glass jar of herbal capsules with green leaves" style="background:linear-gradient(#eef2e6,#dfe6d2)"></div>
    <h3 class="product-name">Herbal supplement pills</h3>
    <div class="product-rating"><svg width="74" height="12" viewBox="0 0 74 12"><g fill="#f3a521"><rect x="0" width="12" height="12"/><rect x="15" width="12" height="12"/><rect x="30" width="12" height="12"/><rect x="45" width="12" height="12"/><rect x="60" width="12" height="12"/></g><g fill="#fff"><path d="M6 2l1.2 2.6 2.8.3-2.1 1.9.6 2.8L6 8.2 3.5 9.6l.6-2.8L2 4.9l2.8-.3z"/><path d="M21 2l1.2 2.6 2.8.3-2.1 1.9.6 2.8L21 8.2l-2.5 1.4.6-2.8L17 4.9l2.8-.3z"/><path d="M36 2l1.2 2.6 2.8.3-2.1 1.9.6 2.8L36 8.2l-2.5 1.4.6-2.8L32 4.9l2.8-.3z"/><path d="M51 2l1.2 2.6 2.8.3-2.1 1.9.6 2.8L51 8.2l-2.5 1.4.6-2.8L47 4.9l2.8-.3z"/><path d="M66 2l1.2 2.6 2.8.3-2.1 1.9.6 2.8L66 8.2l-2.5 1.4.6-2.8L62 4.9l2.8-.3z"/></g></svg>5 REVIEW(S)</div>
    <div class="product-from">from</div>
    <div class="product-price">$13.99 <small>per bottle</small></div>
    <div class="btn-quick">QUICK VIEW</div>
    <div class="btn-cart"><svg width="32" height="32" viewBox="0 0 32 32" aria-hidden="true"><path d="M8 14h16l-2.5 9h-11z" fill="#fff"/><path d="M12 14l3-5M20 14l-3-5" stroke="#fff" stroke-width="1.6"/></svg></div>
  </article>

  <article class="product-card" style="left:751px;top:145px">
    <div class="product-photo" role="img" aria-label="Amber supplement bottle" style="background:linear-gradient(#f3e6dc,#e2c3a8)"></div>
    <h3 class="product-name">Herbal supplement pills</h3>
    <div class="product-rating"><svg width="74" height="12" viewBox="0 0 74 12"><g fill="#f3a521"><rect x="0" width="12" height="12"/><rect x="15" width="12" height="12"/><rect x="30" width="12" height="12"/><rect x="45" width="12" height="12"/><rect x="60" width="12" height="12"/></g><g fill="#fff"><path d="M6 2l1.2 2.6 2.8.3-2.1 1.9.6 2.8L6 8.2 3.5 9.6l.6-2.8L2 4.9l2.8-.3z"/><path d="M21 2l1.2 2.6 2.8.3-2.1 1.9.6 2.8L21 8.2l-2.5 1.4.6-2.8L17 4.9l2.8-.3z"/><path d="M36 2l1.2 2.6 2.8.3-2.1 1.9.6 2.8L36 8.2l-2.5 1.4.6-2.8L32 4.9l2.8-.3z"/><path d="M51 2l1.2 2.6 2.8.3-2.1 1.9.6 2.8L51 8.2l-2.5 1.4.6-2.8L47 4.9l2.8-.3z"/><path d="M66 2l1.2 2.6 2.8.3-2.1 1.9.6 2.8L66 8.2l-2.5 1.4.6-2.8L62 4.9l2.8-.3z"/></g></svg>5 REVIEW(S)</div>
    <div class="product-from">from</div>
    <div class="product-price">$13.99 <small>per bottle</small></div>
    <div class="btn-quick">QUICK VIEW</div>
    <div class="btn-cart"><svg width="32" height="32" viewBox="0 0 32 32" aria-hidden="true"><path d="M8 14h16l-2.5 9h-11z" fill="#fff"/><path d="M12 14l3-5M20 14l-3-5" stroke="#fff" stroke-width="1.6"/></svg></div>
  </article>

  <article class="product-card" style="left:352px;top:388px">
    <div class="product-photo" role="img" aria-label="Open supplement tub with red and blue capsules" style="background:linear-gradient(#eeeff3,#d9dbe3)"></div>
    <h3 class="product-name">Herbal supplement pills</h3>
    <div class="product-rating"><svg width="74" height="12" viewBox="0 0 74 12"><g fill="#f3a521"><rect x="0" width="12" height="12"/><rect x="15" width="12" height="12"/><rect x="30" width="12" height="12"/><rect x="45" width="12" height="12"/><rect x="60" width="12" height="12"/></g><g fill="#fff"><path d="M6 2l1.2 2.6 2.8.3-2.1 1.9.6 2.8L6 8.2 3.5 9.6l.6-2.8L2 4.9l2.8-.3z"/><path d="M21 2l1.2 2.6 2.8.3-2.1 1.9.6 2.8L21 8.2l-2.5 1.4.6-2.8L17 4.9l2.8-.3z"/><path d="M36 2l1.2 2.6 2.8.3-2.1 1.9.6 2.8L36 8.2l-2.5 1.4.6-2.8L32 4.9l2.8-.3z"/><path d="M51 2l1.2 2.6 2.8.3-2.1 1.9.6 2.8L51 8.2l-2.5 1.4.6-2.8L47 4.9l2.8-.3z"/><path d="M66 2l1.2 2.6 2.8.3-2.1 1.9.6 2.8L66 8.2l-2.5 1.4.6-2.8L62 4.9l2.8-.3z"/></g></svg>5 REVIEW(S)</div>
    <div class="product-from">from</div>
    <div class="product-price">$13.99 <small>per bottle</small></div>
    <div class="btn-quick">QUICK VIEW</div>
    <div class="btn-cart"><svg width="32" height="32" viewBox="0 0 32 32" aria-hidden="true"><path d="M8 14h16l-2.5 9h-11z" fill="#fff"/><path d="M12 14l3-5M20 14l-3-5" stroke="#fff" stroke-width="1.6"/></svg></div>
  </article>

  <article class="product-card" style="left:751px;top:388px">
    <div class="product-photo" role="img" aria-label="Two white supplement bottles" style="background:linear-gradient(#f7f7f7,#e6e6e6)"></div>
    <h3 class="product-name">Herbal supplement pills</h3>
    <div class="product-rating"><svg width="74" height="12" viewBox="0 0 74 12"><g fill="#f3a521"><rect x="0" width="12" height="12"/><rect x="15" width="12" height="12"/><rect x="30" width="12" height="12"/><rect x="45" width="12" height="12"/><rect x="60" width="12" height="12"/></g><g fill="#fff"><path d="M6 2l1.2 2.6 2.8.3-2.1 1.9.6 2.8L6 8.2 3.5 9.6l.6-2.8L2 4.9l2.8-.3z"/><path d="M21 2l1.2 2.6 2.8.3-2.1 1.9.6 2.8L21 8.2l-2.5 1.4.6-2.8L17 4.9l2.8-.3z"/><path d="M36 2l1.2 2.6 2.8.3-2.1 1.9.6 2.8L36 8.2l-2.5 1.4.6-2.8L32 4.9l2.8-.3z"/><path d="M51 2l1.2 2.6 2.8.3-2.1 1.9.6 2.8L51 8.2l-2.5 1.4.6-2.8L47 4.9l2.8-.3z"/><path d="M66 2l1.2 2.6 2.8.3-2.1 1.9.6 2.8L66 8.2l-2.5 1.4.6-2.8L62 4.9l2.8-.3z"/></g></svg>5 REVIEW(S)</div>
    <div class="product-from">from</div>
    <div class="product-price">$13.99 <small>per bottle</small></div>
    <div class="btn-quick">QUICK VIEW</div>
    <div class="btn-cart"><svg width="32" height="32" viewBox="0 0 32 32" aria-hidden="true"><path d="M8 14h16l-2.5 9h-11z" fill="#fff"/><path d="M12 14l3-5M20 14l-3-5" stroke="#fff" stroke-width="1.6"/></svg></div>
  </article>

  <article class="product-card" style="left:352px;top:631px">
    <div class="product-photo" role="img" aria-label="White supplement bottle" style="background:linear-gradient(#f7f7f7,#e4e4e4)"></div>
    <h3 class="product-name">Herbal supplement pills</h3>
    <div class="product-rating"><svg width="74" height="12" viewBox="0 0 74 12"><g fill="#f3a521"><rect x="0" width="12" height="12"/><rect x="15" width="12" height="12"/><rect x="30" width="12" height="12"/><rect x="45" width="12" height="12"/><rect x="60" width="12" height="12"/></g><g fill="#fff"><path d="M6 2l1.2 2.6 2.8.3-2.1 1.9.6 2.8L6 8.2 3.5 9.6l.6-2.8L2 4.9l2.8-.3z"/><path d="M21 2l1.2 2.6 2.8.3-2.1 1.9.6 2.8L21 8.2l-2.5 1.4.6-2.8L17 4.9l2.8-.3z"/><path d="M36 2l1.2 2.6 2.8.3-2.1 1.9.6 2.8L36 8.2l-2.5 1.4.6-2.8L32 4.9l2.8-.3z"/><path d="M51 2l1.2 2.6 2.8.3-2.1 1.9.6 2.8L51 8.2l-2.5 1.4.6-2.8L47 4.9l2.8-.3z"/><path d="M66 2l1.2 2.6 2.8.3-2.1 1.9.6 2.8L66 8.2l-2.5 1.4.6-2.8L62 4.9l2.8-.3z"/></g></svg>5 REVIEW(S)</div>
    <div class="product-from">from</div>
    <div class="product-price">$13.99 <small>per bottle</small></div>
    <div class="btn-quick">QUICK VIEW</div>
    <div class="btn-cart"><svg width="32" height="32" viewBox="0 0 32 32" aria-hidden="true"><path d="M8 14h16l-2.5 9h-11z" fill="#fff"/><path d="M12 14l3-5M20 14l-3-5" stroke="#fff" stroke-width="1.6"/></svg></div>
  </article>

  <article class="product-card" style="left:751px;top:631px">
    <div class="product-photo" role="img" aria-label="Brown glass supplement bottle" style="background:linear-gradient(#f1e7e0,#d8c2b2)"></div>
    <h3 class="product-name">Herbal supplement pills</h3>
    <div class="product-rating"><svg width="74" height="12" viewBox="0 0 74 12"><g fill="#f3a521"><rect x="0" width="12" height="12"/><rect x="15" width="12" height="12"/><rect x="30" width="12" height="12"/><rect x="45" width="12" height="12"/><rect x="60" width="12" height="12"/></g><g fill="#fff"><path d="M6 2l1.2 2.6 2.8.3-2.1 1.9.6 2.8L6 8.2 3.5 9.6l.6-2.8L2 4.9l2.8-.3z"/><path d="M21 2l1.2 2.6 2.8.3-2.1 1.9.6 2.8L21 8.2l-2.5 1.4.6-2.8L17 4.9l2.8-.3z"/><path d="M36 2l1.2 2.6 2.8.3-2.1 1.9.6 2.8L36 8.2l-2.5 1.4.6-2.8L32 4.9l2.8-.3z"/><path d="M51 2l1.2 2.6 2.8.3-2.1 1.9.6 2.8L51 8.2l-2.5 1.4.6-2.8L47 4.9l2.8-.3z"/><path d="M66 2l1.2 2.6 2.8.3-2.1 1.9.6 2.8L66 8.2l-2.5 1.4.6-2.8L62 4.9l2.8-.3z"/></g></svg>5 REVIEW(S)</div>
    <div class="product-from">from</div>
    <div class="product-price">$13.99 <small>per bottle</small></div>
    <div class="btn-quick">QUICK VIEW</div>
    <div class="btn-cart"><svg width="32" height="32" viewBox="0 0 32 32" aria-hidden="true"><path d="M8 14h16l-2.5 9h-11z" fill="#fff"/><path d="M12 14l3-5M20 14l-3-5" stroke="#fff" stroke-width="1.6"/></svg></div>
  </article>
</section>

<section class="reviews" role="img" aria-label="Dark blurred backdrop behind customer reviews">
  <h2 class="abs reviews-title">CUSTOMER REVIEWS</h2>
  <svg class="abs" style="left:136px;top:172px" width="24" height="44" viewBox="0 0 24 44" aria-hidden="true"><path d="M20 4L4 22l16 18" fill="none" stroke="#fff" stroke-width="2.5"/></svg>
  <svg class="abs" style="left:1044px;top:172px" width="24" height="44" viewBox="0 0 24 44" aria-hidden="true"><path d="M4 4l16 18L4 40" fill="none" stroke="#555" stroke-width="2.5"/></svg>
  <svg class="abs" style="left:228px;top:122px" width="170" height="168" viewBox="0 0 170 168">
    <polygon role="img" aria-label="Customer portrait" points="4,41 27,2 73,2 96,41 73,80 27,80" fill="#cfae98" stroke="#fff" stroke-width="2"/>
    <polygon role="img" aria-label="Customer portrait" points="72,82 95,43 141,43 164,82 141,121 95,121" fill="#8f7566" stroke="#555" stroke-width="2" opacity=".85"/>
    <polygon role="img" aria-label="Customer portrait" points="4,123 27,84 73,84 96,123 73,162 27,162" fill="#5b4a42" stroke="#555" stroke-width="2" opacity=".8"/>
  </svg>
  <div class="abs review-quote">&ldquo;</div>
  <p class="abs review-text">Suspendisse eu aliquet libero. Nullam faucibus lorem ut rhoncus efficitur. Interdum et malesuada fames ac ante ipsum primis in faucibus. Nam id ligula vel ligula scelerisque hendrerit. Vestibulum lorem dolor, porta vitae sodales id,</p>
  <div class="abs review-name">NAME HEADING<em>City, Location</em></div>
</section>

<footer class="site-footer">
  <div class="footer-heading" style="left:75px">QUICK LINKS</div>
  <ul class="quick-links">
    <li>Home</li>
    <li>Skin Lightening Tablets</li>
    <li>Skin Lightening Creams</li>
    <li>Skin Lightening Soaps</li>
    <li>Skin Lightening Vials</li>
    <li>Contact</li>
    <li>About Us</li>
  </ul>

  <div class="footer-heading" style="left:342px">GET SOCIAL</div>
  <div class="social-link" style="top:130px">lumigram</div>
  <div class="social-link" style="top:176px">Vidora</div>
  <div class="social-link" style="top:219px">chirplo</div>
  <div class="social-link" style="top:263px">Linkwell</div>

  <div class="footer-heading" style="left:558px">CONTACT INFO</div>
  <p class="footer-text" style="left:558px;top:118px;width:290px">Get in touch for expert confidential supplement advice, or for customer services.</p>
  <svg class="phone-icon" style="top:183px" width="34" height="34" viewBox="0 0 34 34" aria-hidden="true"><circle cx="17" cy="17" r="15.5" fill="none" stroke="#fff" stroke-width="2"/><path d="M12 10l3 0 1.5 4-2 1.5c1 2 2.5 3.5 4.5 4.5l1.5-2 4 1.5v3c-7 .5-13-5.5-12.5-12.5z" fill="#fff"/></svg>
  <div class="phone-label" style="top:180px">Calling from the UK</div>
  <div class="phone-number" style="top:196px">0844 000 4172</div>
  <svg class="phone-icon" style="top:238px" width="34" height="34" viewBox="0 0 34 34" aria-hidden="true"><circle cx="17" cy="17" r="15.5" fill="none" stroke="#fff" stroke-width="2"/><path d="M12 10l3 0 1.5 4-2 1.5c1 2 2.5 3.5 4.5 4.5l1.5-2 4 1.5v3c-7 .5-13-5.5-12.5-12.5z" fill="#fff"/></svg>
  <div class="phone-label" style="top:245px">Calling from Overseas</div>
  <div class="phone-number" style="top:261px">+44 844 000 4172</div>

  <p class="footer-text" style="left:889px;top:118px;width:250px">To contact us by email, please click the send us a message tab on the right.</p>
  <p class="footer-text" style="left:889px;top:185px">Our team is available</p>
  <p class="footer-text" style="left:889px;top:206px;font-size:14px;font-weight:700">Monday - Friday: 8am until 18:00pm</p>
  <p class="footer-text" style="left:889px;top:229px">Answerphone out of hours</p>
</footer>
<div class="abs btn-send">SEND US</div>
<div class="abs copyright">Velique &copy; 2016 | All Rights Reserved</div>

</body>
</html>
```